BrivoTerna. Lantern of the Steady Harvest. Business card

Professional business card for BrivoTerna (Lantern of the Steady Harvest)
My rationale: Strategy-> Execution-> Results-> Value that lead to the BrivoTerna name: We put the Lantern of the Steady Harvest.
We deliver value to our customers helping them at defining a good strategy (cyan arrow). 90% of well formulated strategies fail due to poor execution so we also consider strategical execution very important (green arrow). Due to the execution we obtain the results (blue arrow). Finally, the results provide feedback to redefine strategy, and the new strategy has to be executed and new results obtained providing new feedback and on and on. It's like a wheel that finally, must create corporate value: value for shareholders, staholders, employees, providers...-

Target Market(s)

CEOs and steering comitees , invewrnent funds

Industry/Entity Type

Business Consultant

Contact Information for Business Card

Teodoro Vinsquel
CEO & Founder
teodoro.vinsquel@brivoterna-example.com
Mobile: +34 655.803.912
www.brivoterna-example.com

Colors

Designer to choose colors to be used in the design.

Requirements
Nice to have
• Nice to hace the words: Strategy, execution, results
• Nice to vave the claim: Lantern of the Steady Harvest
• The three colors should be shown:
• cyan for STRATEGY
• green for EXECUTION
• blue for RESULTS
Should not have
• Complete black background

```html
<!DOCTYPE html>
<html lang="en">
<head>
<meta charset="utf-8">
<title>BrivoTerna – Business Card</title>
<link href="https://fonts.googleapis.com/css2?family=Open+Sans:wght@400;600;700&display=swap" rel="stylesheet">
<style>
  :root {
    --navy: #223a5e;
    --royal: #0a3a9a;
    --green: #8cc63f;
    --cyan: #13b0ea;
    --white: #ffffff;
    --paper: #ecebe8;
    --text-soft: #e6ebf2;
  }
  * { margin: 0; padding: 0; box-sizing: border-box; }
  html, body {
    width: 1200px; height: 997px; overflow: hidden;
    background: var(--paper);
    font-family: "Open Sans", Arial, sans-serif;
  }
  .sheet {
    position: relative; width: 1200px; height: 997px;
    display: flex; flex-direction: column; align-items: center; justify-content: center; gap: 60px;
  }
  .card {
    position: relative; width: 700px; height: 400px; overflow: hidden;
    box-shadow: 0 6px 18px rgba(0,0,0,0.12);
  }

  /* Front face */
  .card--front { display: flex; background: var(--white); }
  .front-brand {
    width: 300px; display: flex; align-items: center; justify-content: center; gap: 12px;
  }
  .brand-dot { width: 22px; height: 22px; border-radius: 50%; background: var(--royal); }
  .brand-name { font-weight: 700; font-size: 40px; color: var(--royal); letter-spacing: -0.5px; }
  .accent-strip { width: 14px; display: flex; flex-direction: column; }
  .accent-strip span { flex: 1; }
  .accent-strip .results { background: var(--royal); }
  .accent-strip .execution { background: var(--green); }
  .accent-strip .strategy { background: var(--cyan); }
  .front-panel {
    flex: 1; background: var(--navy); color: var(--text-soft);
    display: flex; flex-direction: column; align-items: flex-end; justify-content: flex-end;
    padding: 0 30px 40px 0; text-align: right;
  }
  .person-name { font-weight: 700; font-size: 26px; color: var(--white); line-height: 1.2; }
  .person-role { font-size: 17px; color: var(--green); margin-bottom: 14px; }
  .contact-line { display: flex; align-items: center; gap: 8px; font-size: 15px; line-height: 1.75; }
  .contact-icon { width: 16px; height: 16px; flex: none; }

  /* Back face */
  .card--back {
    background: var(--navy);
    display: flex; align-items: center; justify-content: center; gap: 18px;
  }
  .card--back .brand-dot { width: 30px; height: 30px; background: var(--green); }
  .card--back .brand-name { color: var(--white); font-size: 58px; }
</style>
</head>
<body>
<main class="sheet">
  <section class="card card--front" aria-label="Business card front">
    <div class="front-brand">
      <span class="brand-dot"></span>
      <span class="brand-name">BrivoTerna</span>
    </div>
    <div class="accent-strip">
      <span class="results"></span><span class="execution"></span><span class="strategy"></span>
    </div>
    <div class="front-panel">
      <p class="person-name">Teodoro Vinsquel</p>
      <p class="person-role">CEO &amp; Founder</p>
      <p class="contact-line">+34 655.803.912
        <svg class="contact-icon" viewBox="0 0 16 16"><circle cx="8" cy="8" r="8" fill="#8cc63f"/><path d="M5 4h2l1 2.5-1.2 1a6 6 0 0 0 2.7 2.7l1-1.2L13 10v2a1 1 0 0 1-1 1A8 8 0 0 1 4 5a1 1 0 0 1 1-1z" fill="#223a5e"/></svg>
      </p>
      <p class="contact-line">teodoro.vinsquel@brivoterna-example.com
        <svg class="contact-icon" viewBox="0 0 16 16"><circle cx="8" cy="8" r="8" fill="#8cc63f"/><rect x="4" y="5" width="8" height="6" fill="none" stroke="#223a5e" stroke-width="1.3"/><path d="M4 5l4 3.2L12 5" fill="none" stroke="#223a5e" stroke-width="1.3"/></svg>
      </p>
      <p class="contact-line">www.brivoterna-example.com
        <svg class="contact-icon" viewBox="0 0 16 16"><circle cx="8" cy="8" r="8" fill="#8cc63f"/><circle cx="8" cy="8" r="4.5" fill="none" stroke="#223a5e" stroke-width="1.2"/><path d="M3.5 8h9M8 3.5c-2 2.5-2 6.5 0 9M8 3.5c2 2.5 2 6.5 0 9" fill="none" stroke="#223a5e" stroke-width="1"/></svg>
      </p>
    </div>
  </section>

  <section class="card card--back" aria-label="Business card back">
    <span class="brand-dot"></span>
    <span class="brand-name">BrivoTerna</span>
  </section>
</main>
</body>
</html>
```